Teeth Whitening Clinic Website Redesign - Social Proof Theme

NEW TEETH SITEREVAMP CURRENT WEBSITE:WWW.SANDIEGOSTEETHWHITENING.COMTHEME:SOCIAL PROOF/5 STAR REVIEWS/TESTIMONIALS THEME:https://maps.example.net/QxRvPLoKzN84 I want a testimonial themed, social proof themed website so customers will be sold by testimonials all over the website….I like a nice clean simple site but with all important factors standing out like CALLS TO ACTIONS, for example the $99 special link in header on original design. Also, testimonials throughout the website placed methodically as not to be FORCED and CLUTTEREDKeep all same exact content for all pages and elements of current design. All buttons, calls to action, navigation, etc. Please do not leave anything out from current design. SPECIAL INSTRUCTIONS for banner image:I want to use actual customer photos inside the banner image in a way that really pops and grabs attention. Please grab some customer photos from my PG Account, fk or rateway account: Also, I want to integrate 5 star rateway logo, friendbook review 5 stars icon, searchly business page 5 stars icon, etc. on the banner as well to show social proof as much as possible. Actual customer photos to be used throughout website:https://www.photogram.example/brightharborsmilestudioplace/ https://www.friendbook.com/SDTeethWhitening/https://www.reviewhub.example/biz/bright-harbor-smile-studio-place-bright-harbor-5 Reviews:https://www.reviewhub.example/biz/bright-harbor-smile-studio-place-bright-harbor-5 https://www.friendbook.com/pg/SDTeethWhitening/reviews/?ref=page_internalhttps://goo.gl/maps/TmJcABLAJwC2 Please do home page first to come up with theme then after approval home page we can move forward additional pages.

Target Market(s)

PEOPLE THAT CARE ABOUT DENTAL HYGEINE AND OR CARE ABOUT THEIR TEETH SMILE

Industry/Entity Type

Dental Clinic

Number of Pages Required

5+ page

Colors

Designer to choose colors to be used in the design.

Requirements
Must have
• NEW TEETH SITE
• REVAMP CURRENT WEBSITE:
• WWW.BRIGHTHARBORSMILESTUDIO.EXAMPLE
• THEME:
• SOCIAL PROOF/5 STAR REVIEWS/TESTIMONIALS THEME:
• https://maps.example.net/QxRvPLoKzN84
• I want a testimonial themed, social proof themed website so customers will be sold by testimonials all over the website….I like a nice clean simple site but with all important factors standing out like CALLS TO ACTIONS, for example the $99 special link in header on original design. Also, testimonials throughout the website placed methodically as not to be FORCED and CLUTTERED
• Keep all same exact content for all pages and elements of current design. All buttons, calls to action, navigation, etc. Please do not leave anything out from current design.
• SPECIAL INSTRUCTIONS for banner image:
• I want to use actual customer photos inside the banner image in a way that really pops and grabs attention. Please grab some customer photos from my PG Account, fk or rateway account:
• Also, I want to integrate 5 star rateway logo, friendbook review 5 stars icon, searchly business page 5 stars icon, etc. on the banner as well to show social proof as much as possible.
• Actual customer photos to be used throughout website:
• https://www.photogram.example/brightharborsmilestudioplace/
• https://www.friendbook.example/BHSmileStudio/
• https://www.reviewhub.example/biz/bright-harbor-smile-studio-place-bright-harbor-5
• Reviews:
• https://www.friendbook.example/pg/BHSmileStudio/reviews/?ref=page_internal
• Please do home page first to come up with theme then after approval home page we can move forward additional pages.
Nice to have
• NEW TEETH SITE
• REVAMP CURRENT WEBSITE:
• THEME:
• Reviews:
Should not have
• NEW TEETH SITE
• REVAMP CURRENT WEBSITE:
• THEME:
• Reviews:

```html
<!DOCTYPE html>
<html lang="en">
<head>
<meta charset="utf-8">
<title>Bright Harbor Teeth Whitening – Home Concepts</title>
<link href="https://fonts.googleapis.com/css2?family=Montserrat:wght@500;600;700;800&family=Open+Sans:wght@400;600;700&display=swap" rel="stylesheet">
<style>
:root{
  --teal:#00a3cc;
  --teal-dark:#0086a8;
  --ink:#222;
  --text:#444;
  --muted:#777;
  --board:#e6e6e6;
  --strip:#efefef;
  --soft:#f5f6f6;
  --line:#dcdcdc;
  --black:#000;
  --white:#fff;
}
*{box-sizing:border-box;margin:0;padding:0}
html,body{width:717px;height:1200px;overflow:hidden;background:var(--board)}
body{font-family:"Open Sans",sans-serif;color:var(--text)}
.board{position:absolute;left:0;top:0;width:1484px;height:2484px;transform:scale(.48317);transform-origin:0 0;background:var(--board)}
.page{position:absolute;width:673px;height:2380px;background:var(--white);box-shadow:0 2px 8px rgba(0,0,0,.12);overflow:hidden}
.page--a{left:57px;top:62px}
.page--b{left:760px;top:44px}
.abs{position:absolute}

/* header */
.brand{left:80px;top:15px;display:flex;align-items:center;gap:6px}
.brand__mark{width:30px;height:30px;border-radius:50%;border:2px solid #bbb}
.brand__name{font-family:"Montserrat",sans-serif;font-weight:600;font-size:11px;color:#555;line-height:1}
.brand__name small{display:block;font-size:6px;color:var(--teal);font-weight:500;margin-top:2px}
.book-btn{left:464px;top:10px;width:130px;height:20px;border:1.5px solid var(--teal);border-radius:10px;color:var(--teal);font-size:7px;display:flex;align-items:center;justify-content:center}
.nav{right:80px;top:38px;display:flex;gap:7px;font-size:7px;color:#333}
.promo{left:0;top:58px;width:673px;height:40px;background:var(--black);color:var(--teal);font-weight:700;font-size:10px;display:flex;align-items:center;justify-content:center}

/* hero */
.hero{left:0;top:98px;width:673px;height:245px;display:grid;grid-template-columns:repeat(4,1fr);grid-template-rows:1fr 1fr}
.tile-photo{background:linear-gradient(160deg,#d9d3cc,#9d8f86 60%,#5d5450)}
.tile-tint{background:linear-gradient(160deg,#37bde0,#16a7d1)}
.hero__text{left:0;top:98px;width:336px;height:245px;background:linear-gradient(160deg,#37bde0,#15a4cf);padding:65px 0 0 80px;font-family:"Montserrat",sans-serif;font-weight:800;font-size:23px;line-height:32px;color:var(--white)}
.hero__photos{left:336px;top:98px;width:337px;height:245px;display:grid;grid-template-columns:1fr 1fr;grid-template-rows:110px 135px}

/* review strip */
.reviews{left:0;top:343px;width:673px;background:var(--strip);display:flex;justify-content:center;align-items:center;gap:60px}
.page--a .reviews{height:65px}
.page--b .reviews{height:93px}
.review{display:flex;align-items:center;gap:5px;font-family:"Montserrat",sans-serif;font-weight:700;font-size:13px;color:#555}
.review i{display:block;width:11px;height:11px;border-radius:50%;background:#999}
.review small{display:block;font-size:6px;color:#999;letter-spacing:1px;font-weight:600}

/* intro */
.h2{font-family:"Montserrat",sans-serif;font-weight:500;font-size:18px;color:var(--ink)}
.lead{color:var(--teal);font-size:8px;font-weight:600}
.para{font-size:6.6px;line-height:14.4px;color:#555;text-align:justify}
.btn{display:inline-flex;align-items:center;justify-content:center;background:var(--teal);color:var(--white);font-weight:700;font-size:7px;border-radius:11px;height:21px;padding:0 12px;gap:5px}
.intro{left:80px;top:470px;width:240px}
.intro .h2{margin-left:4px}
.intro .lead{margin:6px 0 6px}
.intro .btn{margin-top:6px}
.video{left:342px;top:476px;width:252px;height:162px;background:linear-gradient(135deg,#e8e6ea,#b4aab0 55%,#6c5f6a)}
.play{position:absolute;left:108px;top:63px;width:36px;height:36px}

.how-photo{left:80px;top:722px;width:357px;height:266px;background:linear-gradient(135deg,#cfc3c0,#8d7c7b 55%,#4e4244);box-shadow:0 4px 8px rgba(0,0,0,.2)}
.how-card{left:274px;top:754px;width:320px;height:202px;background:var(--white);border:1px solid #eee;box-shadow:0 1px 4px rgba(0,0,0,.06);padding:20px 26px}
.how-card .para{margin-top:6px}
.how-card .para + .para{margin-top:6px}
.how-card .btn{margin-top:9px}

/* why */
.why{left:0;top:1051px;width:673px;height:164px;background:var(--teal);color:var(--white);text-align:center;padding-top:44px}
.why .h2{color:var(--white)}
.why p{font-size:9.5px;line-height:18px;margin-top:14px;font-weight:600}
.why-diagram{left:0;top:1215px;width:673px;height:248px}

/* compare */
.compare{left:0;top:1463px;width:673px;height:383px;background:var(--soft);text-align:center;padding-top:42px}
.compare p{font-size:6.6px;color:#666;margin-top:8px}
.table{left:67px;top:1566px;display:flex;gap:2px;align-items:flex-start}
.col{width:103px;background:var(--white);border:1px solid #e4e4e4;font-size:7.6px;color:#444}
.col__head{height:42px;background:var(--black);color:var(--white);font-family:"Montserrat",sans-serif;font-weight:600;font-size:10.5px;display:flex;align-items:center;justify-content:center}
.col__cell{height:32.4px;display:flex;align-items:center;justify-content:center;border-top:1px solid #e8e8e8}
.col__cell:first-of-type{border-top:0}
.col--std{margin-top:11px}
.col--hi{width:124px;box-shadow:0 2px 8px rgba(0,0,0,.12)}
.col--hi .col__head{height:53px;background:var(--teal);flex-direction:column;font-size:12px}
.col--hi .col__head small{font-family:"Open Sans",sans-serif;font-size:5px;font-weight:400;margin-top:3px}
.col--hi .col__cell{margin:0 12px}
.col--hi .col__cell:first-of-type{margin-top:6px}
.col--hi .col__cell:last-child{margin-bottom:4px}

/* testimonials */
.testi{left:0;top:1846px;width:673px;height:267px;background:linear-gradient(180deg,#0b9ec6,#0a86aa);color:var(--white);text-align:center;padding-top:50px}
.testi .h2{color:var(--white);font-size:19px}
.testi__sub{font-size:6.6px;margin-top:4px}
.testi__quote{font-size:8px;font-weight:700;line-height:14.6px;width:340px;margin:16px auto 0}
.quote-bump{left:310px;top:1828px;width:52px;height:40px;border-radius:50%;background:var(--white)}
.avatars{left:0;top:2003px;width:673px;display:flex;justify-content:center;align-items:center;gap:18px}
.avatar{width:32px;height:32px;border-radius:50%;border:2px solid var(--white);background:linear-gradient(135deg,#d8d8d8,#7a7a7a)}
.avatar--main{width:48px;height:48px;margin:0 6px;background:linear-gradient(135deg,#cfe3ee,#8a9aa4)}
.testi__rule{left:160px;top:2056px;width:354px;height:1px;background:rgba(255,255,255,.6)}
.testi__name{left:0;top:2062px;width:673px;text-align:center;color:var(--white);font-size:9px}

/* footer */
.contact{top:2158px;width:160px;text-align:center}
.contact h4{font-weight:600;font-size:9px;color:#444;display:flex;align-items:center;justify-content:center;gap:5px}
.contact p{font-size:5.4px;color:#777;line-height:8.5px;margin-top:4px}
.rule{left:80px;width:514px;height:1px;background:var(--line)}
.links{top:2226px;font-size:6.6px;color:#666;line-height:16.2px}
.stay{left:513px;top:2226px;font-size:8.5px;color:#444;font-weight:600}
.socials{left:518px;top:2260px;display:flex;gap:13px}
.socials i{display:block;width:12px;height:12px;border-radius:50%;border:1px solid #ccc}
.need{left:513px;top:2284px;width:80px}
.copy{left:0;top:2354px;width:650px;text-align:center;font-size:6.6px;color:#555}
</style>
</head>
<body>
<div class="board">

<!-- Concept A -->
<section class="page page--a">
  <div class="abs brand"><span class="brand__mark"></span><span class="brand__name">BRIGHT HARBOR<small>Teeth Whitening Center</small></span></div>
  <div class="abs book-btn">&#9635;&nbsp; Book Appointment Online</div>
  <nav class="abs nav"><span>Home</span><span>Our Process</span><span>Photos</span><span>Free Treatments</span><span>Testimonials</span><span>Blog</span><span>FAQ</span><span>Contact</span><span>Gift Certificates</span></nav>
  <div class="abs promo">Click Here to Get Our $99 Teeth, Whiting Deal (Reg: $378)</div>

  <div class="abs hero__text" role="img" aria-label="Tinted collage of smiling customers behind the headline">GET THAT WHITE<br>SMILE YOU’VE<br>ALWAYS WANTED</div>
  <div class="abs hero__photos">
    <div class="tile-photo" role="img" aria-label="Customers posing with smile signs"></div>
    <div class="tile-photo" role="img" aria-label="Group of happy customers"></div>
    <div class="tile-photo" role="img" aria-label="Customers holding a smile accessory sign"></div>
    <div class="tile-photo" role="img" aria-label="Customer with a bright smile sign"></div>
  </div>

  <div class="abs reviews">
    <div class="review">rateway<i></i></div>
    <div class="review"><div>friendbook<small>★★★★★</small></div></div>
    <div class="review"><div>searchly<small>★★★★★</small></div><i></i></div>
  </div>

  <div class="abs intro">
    <h2 class="h2">BRIGHT HARBOR CENTER</h2>
    <p class="lead">The best price, service and results.</p>
    <p class="para">Bright Harbor Teeth Whitening Center features state-of-the-art technologies that are safe, industry-unique and very cost-effective. Our teeth whitening system utilizes the latest blue light whitening technology. Our Blue Light Systems are calibrated precisely for optimal activation of our exclusive hydrogen peroxide based whitening solution which is manufactured in a FDA registered facility in the USA.</p>
    <span class="btn">Read More</span>
  </div>
  <div class="abs video" role="img" aria-label="Video still of a whitening treatment">
    <svg class="play" viewBox="0 0 36 36"><circle cx="18" cy="18" r="16" fill="none" stroke="#fff" stroke-width="1.5"/><path d="M14 11l11 7-11 7z" fill="none" stroke="#fff" stroke-width="1.5"/></svg>
  </div>

  <div class="abs how-photo" role="img" aria-label="Technician preparing a whitening treatment"></div>
  <div class="abs how-card">
    <h2 class="h2">HOW IT WORKS</h2>
    <p class="para">We have a very effective teeth whitening treatment that is guaranteed to get you quick results in about 1 hour. To start the treatment you'll apply a Hydrogen Peroxide based whitening agent to your teeth. We then place our cold blue light directly in front of your exposed teeth for 15 minutes per treatment.</p>
    <p class="para">The lighting systems we use activate the whitening agent and thats what accelerates the whitening process, giving you whiter teeth in less than an hour.</p>
    <span class="btn">Read More</span>
  </div>

  <div class="abs why">
    <h2 class="h2">WHY CHOOSE US</h2>
    <p>Sed ut perspiciatis unde omnis iste natus aerror sit voluptatem accusantium dolor<br>aemque laudantium, totam rem aperiam, eaque ipsa quae</p>
  </div>
  <svg class="abs why-diagram" viewBox="0 0 673 248" font-family="Montserrat, sans-serif" font-size="8" font-weight="700" fill="#333" text-anchor="middle">
    <path d="M257 0a79 79 0 0 0 158 0z" fill="#00a3cc"/>
    <circle cx="336" cy="30" r="26" fill="#fff"/>
    <path d="M325 20c4-5 18-5 22 0 3 5 0 12-2 18-1 5-3 10-5 4l-2-6-2 6c-2 6-4 1-5-4-2-6-5-13-6-18z" fill="none" stroke="#00a3cc" stroke-width="1.6"/>
    <g stroke="#aaa" stroke-dasharray="2 2" fill="none">
      <path d="M190 24L255 6M236 75L268 42M290 120L300 60M380 120L370 60M440 72L405 42M500 24L432 6"/>
    </g>
    <g fill="#00a3cc"><circle cx="202" cy="20" r="2.5"/><circle cx="233" cy="76" r="2.5"/><circle cx="296" cy="112" r="2.5"/><circle cx="376" cy="112" r="2.5"/><circle cx="438" cy="76" r="2.5"/><circle cx="479" cy="17" r="2.5"/></g>
    <g fill="#fff" style="filter:drop-shadow(0 1px 3px rgba(0,0,0,.18))">
      <circle cx="168" cy="28" r="22"/><circle cx="209" cy="102" r="22"/><circle cx="290" cy="143" r="22"/><circle cx="380" cy="143" r="22"/><circle cx="462" cy="95" r="22"/><circle cx="510" cy="28" r="22"/>
    </g>
    <g fill="none" stroke="#00a3cc" stroke-width="1.3">
      <path d="M160 28l8-8h8v8l-8 8z"/><path d="M502 28l8-8h8v8l-8 8z"/>
      <rect x="201" y="96" width="10" height="12"/><circle cx="214" cy="98" r="4"/>
      <circle cx="290" cy="139" r="5"/><path d="M283 152c2-5 12-5 14 0"/>
      <rect x="373" y="144" width="14" height="6"/><circle cx="380" cy="137" r="4"/>
      <path d="M454 104l14-16"/>
    </g>
    <text x="168" y="68">PRICE</text><text x="209" y="142">RESULT</text><text x="290" y="183">NO PAIN</text><text x="380" y="183">SERVICE</text><text x="462" y="135">CONVENIENCE</text><text x="510" y="68">PRICE</text>
  </svg>

  <div class="abs compare">
    <h2 class="h2">COMPARE US</h2>
    <p>Sed ut perspiciatis unde omnis iste natus error sit voluptatem accus</p>
  </div>
  <div class="abs table">
    <div class="col col--std"><div class="col__head">FEATURES</div><div class="col__cell">Speed</div><div class="col__cell">Ease of Use</div><div class="col__cell">Cost</div><div class="col__cell">Availability</div><div class="col__cell">Pain</div></div>
    <div class="col col--std"><div class="col__head">LUMAPRO</div><div class="col__cell">1-2 Hours</div><div class="col__cell">Difficult / Dentist</div><div class="col__cell">$300 - $600</div><div class="col__cell">Limited Availability</div><div class="col__cell">Pain &amp; Sensitivity</div></div>
    <div class="col col--hi"><div class="col__head">BRIGHTHARBOR<small>Teeth Whitening Center</small></div><div class="col__cell">45 Mins</div><div class="col__cell">Very Easy</div><div class="col__cell">$378</div><div class="col__cell">Appt Only</div><div class="col__cell">No Pain</div></div>
    <div class="col col--std"><div class="col__head">GLEAMLINE</div><div class="col__cell">7-14 Days</div><div class="col__cell">Difficult / Dentist</div><div class="col__cell">$300 - $600</div><div class="col__cell">Limited Availability</div><div class="col__cell">Sensitivity</div></div>
    <div class="col col--std"><div class="col__head">HOME KITS</div><div class="col__cell">7-30 Days</div><div class="col__cell">Difficult</div><div class="col__cell">$50 - $150</div><div class="col__cell">Store Purchase</div><div class="col__cell">Sensitivity</div></div>
  </div>

  <div class="abs testi">
    <h2 class="h2">TESTIMONIALS</h2>
    <p class="testi__sub">Our happy 1000+ clients feedback</p>
    <p class="testi__quote">Today I came to do my teeth whitening. The staff is really friendly and welcoming and Renata did such a good job with my smile! I will come back for more services in the future :)</p>
  </div>
  <div class="abs quote-bump"></div>
  <svg class="abs" style="left:326px;top:1848px" width="20" height="14" viewBox="0 0 20 14"><path d="M2 14V8c0-4 2-7 6-8v3c-2 1-3 2-3 4h3v7zM12 14V8c0-4 2-7 6-8v3c-2 1-3 2-3 4h3v7z" fill="#00a3cc"/></svg>
  <svg class="abs" style="left:146px;top:1942px" width="26" height="18" viewBox="0 0 20 14"><path d="M2 14V8c0-4 2-7 6-8v3c-2 1-3 2-3 4h3v7zM12 14V8c0-4 2-7 6-8v3c-2 1-3 2-3 4h3v7z" fill="#fff"/></svg>
  <svg class="abs" style="left:62px;top:2002px" width="16" height="26" viewBox="0 0 16 26"><path d="M13 2L3 13l10 11" stroke="#fff" stroke-width="2.5" fill="none"/></svg>
  <svg class="abs" style="left:596px;top:2002px" width="16" height="26" viewBox="0 0 16 26"><path d="M3 2l10 11L3 24" stroke="#fff" stroke-width="2.5" fill="none"/></svg>
  <div class="abs avatars">
    <span class="avatar" role="img" aria-label="Customer portrait"></span><span class="avatar" role="img" aria-label="Customer portrait"></span><span class="avatar avatar--main" role="img" aria-label="Featured customer portrait"></span><span class="avatar" role="img" aria-label="Customer portrait"></span><span class="avatar" role="img" aria-label="Customer portrait"></span>
  </div>
  <div class="abs testi__rule"></div>
  <div class="abs testi__name">- Marisol T.</div>

  <div class="abs contact" style="left:72px"><h4>&#9990; Give Us a Call</h4><p>24 hrs support center ready<br>o help you call Us...</p></div>
  <div class="abs contact" style="left:243px"><h4>&#9993; Send Us Email</h4><p>Contact Us &amp; we'll help<br>you with pleasure...</p></div>
  <div class="abs contact" style="left:414px"><h4>&#9711; Chat With Us</h4><p>Instantly get help an online<br>dedicated personnel...</p></div>
  <div class="abs rule" style="top:2205px"></div>
  <div class="abs links" style="left:84px">Home<br>Book Appointment<br>Our Process<br>Photos<br>Testimonials</div>
  <div class="abs links" style="left:190px">Contact Us<br>FAQ<br>After Care<br>Blog<br>Gift Certificates</div>
  <div class="abs links" style="left:288px">Consent Form Espanol<br>Consent Form English<br>Cancellation Policy<br>Privacy Policy<br>Free Treatments</div>
  <div class="abs links" style="left:413px">About Us<br>How It Works<br>Why Choose Us<br>Compare Us<br>Our Videos</div>
  <div class="abs stay">Stay in Touch</div>
  <div class="abs socials"><i></i><i></i><i></i></div>
  <span class="abs btn need">Need Help &#9900;</span>
  <div class="abs rule" style="top:2342px"></div>
  <div class="abs copy">Copyright © 2018. All Rights Reserved.</div>
</section>

<!-- Concept B -->
<section class="page page--b">
  <div class="abs brand"><span class="brand__mark"></span><span class="brand__name">BRIGHT HARBOR<small>Teeth Whitening Center</small></span></div>
  <div class="abs book-btn">&#9635;&nbsp; Book Appointment Online</div>
  <nav class="abs nav"><span>Home</span><span>Our Process</span><span>Photos</span><span>Free Treatments</span><span>Testimonials</span><span>Blog</span><span>FAQ</span><span>Contact</span><span>Gift Certificates</span></nav>
  <div class="abs promo">Click Here to Get Our $99 Teeth, Whiting Deal (Reg: $378)</div>

  <div class="abs hero">
    <div class="tile-tint" role="img" aria-label="Tinted customer photo"></div>
    <div class="tile-photo" role="img" aria-label="Customers holding a smile with cheer sign"></div>
    <div class="tile-tint" role="img" aria-label="Tinted customer photo"></div>
    <div class="tile-photo" role="img" aria-label="Group of smiling customers"></div>
    <div class="tile-photo" role="img" aria-label="Two customers with a love my smile sign"></div>
    <div class="tile-tint" role="img" aria-label="Tinted customer photo"></div>
    <div class="tile-photo" role="img" aria-label="Customers with a smile accessory sign"></div>
    <div class="tile-tint" role="img" aria-label="Tinted customer photo"></div>
  </div>

  <div class="abs reviews">
    <div class="review">rateway<i></i></div>
    <div class="review"><div>friendbook<small>★★★★★</small></div></div>
    <div class="review"><div>searchly<small>★★★★★</small></div><i></i></div>
  </div>

  <div class="abs intro">
    <h2 class="h2">BRIGHT HARBOR CENTER</h2>
    <p class="lead">The best price, service and results.</p>
    <p class="para">Bright Harbor Teeth Whitening Center features state-of-the-art technologies that are safe, industry-unique and very cost-effective. Our teeth whitening system utilizes the latest blue light whitening technology. Our Blue Light Systems are calibrated precisely for optimal activation of our exclusive hydrogen peroxide based whitening solution which is manufactured in a FDA registered facility in the USA.</p>
    <span class="btn">Read More</span>
  </div>
  <div class="abs video" role="img" aria-label="Video still of a whitening treatment">
    <svg class="play" viewBox="0 0 36 36"><circle cx="18" cy="18" r="16" fill="none" stroke="#fff" stroke-width="1.5"/><path d="M14 11l11 7-11 7z" fill="none" stroke="#fff" stroke-width="1.5"/></svg>
  </div>

  <div class="abs how-photo" role="img" aria-label="Technician preparing a whitening treatment"></div>
  <div class="abs how-card">
    <h2 class="h2">HOW IT WORKS</h2>
    <p class="para">We have a very effective teeth whitening treatment that is guaranteed to get you quick results in about 1 hour. To start the treatment you'll apply a Hydrogen Peroxide based whitening agent to your teeth. We then place our cold blue light directly in front of your exposed teeth for 15 minutes per treatment.</p>
    <p class="para">The lighting systems we use activate the whitening agent and thats what accelerates the whitening process, giving you whiter teeth in less than an hour.</p>
    <span class="btn">Read More</span>
  </div>

  <div class="abs why">
    <h2 class="h2">WHY CHOOSE US</h2>
    <p>Sed ut perspiciatis unde omnis iste natus aerror sit voluptatem accusantium dolor<br>aemque laudantium, totam rem aperiam, eaque ipsa quae</p>
  </div>
  <svg class="abs why-diagram" viewBox="0 0 673 248" font-family="Montserrat, sans-serif" font-size="8" font-weight="700" fill="#333" text-anchor="middle">
    <path d="M257 0a79 79 0 0 0 158 0z" fill="#00a3cc"/>
    <circle cx="336" cy="30" r="26" fill="#fff"/>
    <path d="M325 20c4-5 18-5 22 0 3 5 0 12-2 18-1 5-3 10-5 4l-2-6-2 6c-2 6-4 1-5-4-2-6-5-13-6-18z" fill="none" stroke="#00a3cc" stroke-width="1.6"/>
    <g stroke="#aaa" stroke-dasharray="2 2" fill="none">
      <path d="M190 24L255 6M236 75L268 42M290 120L300 60M380 120L370 60M440 72L405 42M500 24L432 6"/>
    </g>
    <g fill="#00a3cc"><circle cx="202" cy="20" r="2.5"/><circle cx="233" cy="76" r="2.5"/><circle cx="296" cy="112" r="2.5"/><circle cx="376" cy="112" r="2.5"/><circle cx="438" cy="76" r="2.5"/><circle cx="479" cy="17" r="2.5"/></g>
    <g fill="#fff" style="filter:drop-shadow(0 1px 3px rgba(0,0,0,.18))">
      <circle cx="168" cy="28" r="22"/><circle cx="209" cy="102" r="22"/><circle cx="290" cy="143" r="22"/><circle cx="380" cy="143" r="22"/><circle cx="462" cy="95" r="22"/><circle cx="510" cy="28" r="22"/>
    </g>
    <g fill="none" stroke="#00a3cc" stroke-width="1.3">
      <path d="M160 28l8-8h8v8l-8 8z"/><path d="M502 28l8-8h8v8l-8 8z"/>
      <rect x="201" y="96" width="10" height="12"/><circle cx="214" cy="98" r="4"/>
      <circle cx="290" cy="139" r="5"/><path d="M283 152c2-5 12-5 14 0"/>
      <rect x="373" y="144" width="14" height="6"/><circle cx="380" cy="137" r="4"/>
      <path d="M454 104l14-16"/>
    </g>
    <text x="168" y="68">PRICE</text><text x="209" y="142">RESULT</text><text x="290" y="183">NO PAIN</text><text x="380" y="183">SERVICE</text><text x="462" y="135">CONVENIENCE</text><text x="510" y="68">PRICE</text>
  </svg>

  <div class="abs compare">
    <h2 class="h2">COMPARE US</h2>
    <p>Sed ut perspiciatis unde omnis iste natus error sit voluptatem accus</p>
  </div>
  <div class="abs table">
    <div class="col col--std"><div class="col__head">FEATURES</div><div class="col__cell">Speed</div><div class="col__cell">Ease of Use</div><div class="col__cell">Cost</div><div class="col__cell">Availability</div><div class="col__cell">Pain</div></div>
    <div class="col col--std"><div class="col__head">LUMAPRO</div><div class="col__cell">1-2 Hours</div><div class="col__cell">Difficult / Dentist</div><div class="col__cell">$300 - $600</div><div class="col__cell">Limited Availability</div><div class="col__cell">Pain &amp; Sensitivity</div></div>
    <div class="col col--hi"><div class="col__head">BRIGHTHARBOR<small>Teeth Whitening Center</small></div><div class="col__cell">45 Mins</div><div class="col__cell">Very Easy</div><div class="col__cell">$378</div><div class="col__cell">Appt Only</div><div class="col__cell">No Pain</div></div>
    <div class="col col--std"><div class="col__head">GLEAMLINE</div><div class="col__cell">7-14 Days</div><div class="col__cell">Difficult / Dentist</div><div class="col__cell">$300 - $600</div><div class="col__cell">Limited Availability</div><div class="col__cell">Sensitivity</div></div>
    <div class="col col--std"><div class="col__head">HOME KITS</div><div class="col__cell">7-30 Days</div><div class="col__cell">Difficult</div><div class="col__cell">$50 - $150</div><div class="col__cell">Store Purchase</div><div class="col__cell">Sensitivity</div></div>
  </div>

  <div class="abs testi">
    <h2 class="h2">TESTIMONIALS</h2>
    <p class="testi__sub">Our happy 1000+ clients feedback</p>
    <p class="testi__quote">Today I came to do my teeth whitening. The staff is really friendly and welcoming and Renata did such a good job with my smile! I will come back for more services in the future :)</p>
  </div>
  <div class="abs quote-bump"></div>
  <svg class="abs" style="left:326px;top:1848px" width="20" height="14" viewBox="0 0 20 14"><path d="M2 14V8c0-4 2-7 6-8v3c-2 1-3 2-3 4h3v7zM12 14V8c0-4 2-7 6-8v3c-2 1-3 2-3 4h3v7z" fill="#00a3cc"/></svg>
  <svg class="abs" style="left:146px;top:1942px" width="26" height="18" viewBox="0 0 20 14"><path d="M2 14V8c0-4 2-7 6-8v3c-2 1-3 2-3 4h3v7zM12 14V8c0-4 2-7 6-8v3c-2 1-3 2-3 4h3v7z" fill="#fff"/></svg>
  <svg class="abs" style="left:62px;top:2002px" width="16" height="26" viewBox="0 0 16 26"><path d="M13 2L3 13l10 11" stroke="#fff" stroke-width="2.5" fill="none"/></svg>
  <svg class="abs" style="left:596px;top:2002px" width="16" height="26" viewBox="0 0 16 26"><path d="M3 2l10 11L3 24" stroke="#fff" stroke-width="2.5" fill="none"/></svg>
  <div class="abs avatars">
    <span class="avatar" role="img" aria-label="Customer portrait"></span><span class="avatar" role="img" aria-label="Customer portrait"></span><span class="avatar avatar--main" role="img" aria-label="Featured customer portrait"></span><span class="avatar" role="img" aria-label="Customer portrait"></span><span class="avatar" role="img" aria-label="Customer portrait"></span>
  </div>
  <div class="abs testi__rule"></div>
  <div class="abs testi__name">- Marisol T.</div>

  <div class="abs contact" style="left:72px"><h4>&#9990; Give Us a Call</h4><p>24 hrs support center ready<br>o help you call Us...</p></div>
  <div class="abs contact" style="left:243px"><h4>&#9993; Send Us Email</h4><p>Contact Us &amp; we'll help<br>you with pleasure...</p></div>
  <div class="abs contact" style="left:414px"><h4>&#9711; Chat With Us</h4><p>Instantly get help an online<br>dedicated personnel...</p></div>
  <div class="abs rule" style="top:2205px"></div>
  <div class="abs links" style="left:84px">Home<br>Book Appointment<br>Our Process<br>Photos<br>Testimonials</div>
  <div class="abs links" style="left:190px">Contact Us<br>FAQ<br>After Care<br>Blog<br>Gift Certificates</div>
  <div class="abs links" style="left:288px">Consent Form Espanol<br>Consent Form English<br>Cancellation Policy<br>Privacy Policy<br>Free Treatments</div>
  <div class="abs links" style="left:413px">About Us<br>How It Works<br>Why Choose Us<br>Compare Us<br>Our Videos</div>
  <div class="abs stay">Stay in Touch</div>
  <div class="abs socials"><i></i><i></i><i></i></div>
  <span class="abs btn need">Need Help &#9900;</span>
  <div class="abs rule" style="top:2342px"></div>
  <div class="abs copy">Copyright © 2018. All Rights Reserved.</div>
</section>

</div>
</body>
</html>
```